Web Design job - Condo Debts Collection Business needs a Web Design

I need a site for a client, who works with condo debts collection, and ensure all revenues provided by condo fees will be always available to the building manager of condo on a specific date, regardless of defaults.
I have the visual identity (logo, slogan and colors) of the company, and some requirements on layout (kind of slider, menu options, phone number on a noble position, etc) - maybe I can do a sketch, but I like the idea of give some freedom to designer.

*** PLEASE, we have no interest in templates. We want something new***

Target Market(s)

I have two targets for this design: - Condominium's building manager. This target is looking for a solution to overdue debts on it's condo. - Residents on condominiums. This target wants to live in a better place, where their neighbors pay their condominium fees on time.

Number of Pages Required

1 page

Requirements
Must have
• - Slider with title, some short text related, a nice image (I prefer happy and/or peaceful family, people doing business, happy friends, and so on).
• - I have a special attention to menu. I'm looking for one I can have a nice effect, more elegant, charming, kind of innovative.
• - Phone number on the top (or clearly visible).
• - Member log in area or icon on the top (or clearly visible).
• - News/articles area.
• - Modern fonts, with good quality, sans-serif on areas where reading is more intensive (prefer Google web-fonts).
• - Colors specified on attached files.
Nice to have
• - Clear background color, cause it's better to read larger texts (like articles). Dark backgrounds makes reading difficult.
• - A site with effects (like shadows, lines, curves, gradients, lights) is usually pretty.
• - I pay attention on beautiful footers.
Should not have
• - Images with a lot of money (I don't sell richness, I sell tranquility, peace, harmony, safety).
• - Poor menu.

```html
<!DOCTYPE html>
<html lang="en">
<head>
<meta charset="utf-8">
<title>Calmora – Condominium Fee Collection</title>
<link href="https://fonts.googleapis.com/css2?family=Alegreya:ital,wght@0,400;0,500;0,700;1,400;1,500&family=Montserrat:wght@700;800&family=Open+Sans:wght@400;600;700&display=swap" rel="stylesheet">
<style>
  :root{
    --gold:#e8a317;
    --gold-soft:#f2cf85;
    --ink:#2b2b2b;
    --text:#6d6d6d;
    --muted:#9a9a9a;
    --icon:#777777;
    --paper:#ffffff;
    --night:#232323;
    --night-line:#3a3a3a;
    --night-text:#b5b5b5;
  }
  *{box-sizing:border-box;margin:0;padding:0}
  html,body{width:1200px;height:3528px;overflow:hidden}
  body{position:relative;background:var(--paper);font-family:"Open Sans",sans-serif;color:var(--text)}
  .abs{position:absolute}
  .brand{font-family:"Montserrat",sans-serif;font-weight:800;color:var(--ink);letter-spacing:-1px}
  .btn{display:inline-block;background:var(--gold);color:#fff;font-weight:700;font-size:15px;border-radius:22px;padding:11px 28px;font-family:"Alegreya",serif}

  /* header */
  .call{left:44px;top:38px;display:flex;align-items:center;gap:16px}
  .call-icon{width:50px;height:50px;border:2px solid var(--gold);border-radius:50%;display:flex;align-items:center;justify-content:center}
  .call-label{font-size:14px;color:var(--muted);font-weight:600}
  .call-number{font-size:20px;color:var(--gold);font-weight:700}
  .logo{left:0;width:1200px;top:36px;display:flex;justify-content:center;align-items:center;gap:14px}
  .logo-mark{width:34px;height:34px;background:var(--gold)}
  .logo-name{font-size:44px;line-height:1}
  .login{right:44px;top:44px;background:var(--gold);color:#fff;font-size:14px;font-weight:700;padding:13px 30px;border-radius:24px;letter-spacing:.5px}

  .nav{top:132px;left:0;width:1200px;height:50px;background:var(--gold);display:flex;justify-content:center;align-items:center;gap:72px}
  .nav a{color:#fff;text-decoration:none;font-size:14px;font-weight:700;letter-spacing:.6px}

  /* hero */
  .hero-photo{top:182px;left:0;width:1200px;height:590px;background:linear-gradient(100deg,#f7f5f1 0%,#f3efe8 30%,#d9b79a 55%,#b98a68 75%,#e8ddc9 100%);clip-path:polygon(0 0,100% 0,100% 86%,48% 100%,0 88%)}
  .hero-copy{top:300px;left:84px;width:380px}
  .hero-title{font-size:92px;line-height:1;margin-bottom:26px}
  .hero-copy p{font-size:15px;line-height:1.7;margin-bottom:34px}

  /* section titles */
  .sec-title{left:0;width:1200px;text-align:center;font-family:"Alegreya",serif;font-style:italic;font-size:44px;color:var(--ink)}
  .sec-rule{left:570px;width:60px;height:3px;background:var(--gold)}
  .sec-sub{left:300px;width:600px;text-align:center;font-size:13px;color:var(--muted)}

  /* welcome */
  .welcome-photo{top:900px;left:180px;width:420px;height:288px;background:linear-gradient(160deg,#d7b98a,#a87c4f 60%,#6f7a3d);box-shadow:0 10px 24px rgba(0,0,0,.18)}
  .welcome-copy{top:914px;left:672px;width:440px}
  .welcome-copy h2{font-family:"Alegreya",serif;font-size:36px;color:var(--ink);font-weight:500;margin-bottom:12px}
  .welcome-copy .rule{width:60px;height:3px;background:var(--gold);margin-bottom:24px}
  .welcome-copy p{font-size:14px;line-height:1.8;margin-bottom:30px}

  /* services */
  .card{top:1432px;width:320px;height:376px;background:var(--paper);box-shadow:0 4px 18px rgba(0,0,0,.1);text-align:center;padding:56px 36px 0}
  .card.active{border-bottom:6px solid var(--gold)}
  .card-icon{width:80px;height:80px;margin:0 auto 10px;border-radius:50%;border:3px solid var(--gold);display:flex;align-items:center;justify-content:center}
  .card.active .card-icon{background:var(--gold)}
  .card h3{font-family:"Alegreya",serif;font-style:italic;font-weight:500;font-size:22px;color:var(--ink);margin:26px 0 10px}
  .card .rule{width:44px;height:2px;background:var(--gold);margin:0 auto 22px}
  .card p{font-size:13px;line-height:1.8}

  /* testimonial */
  .testi-photo{top:1904px;left:0;width:1200px;height:480px;background:linear-gradient(90deg,#c9a36a,#a88b4e 35%,#7f8a3b 65%,#b7a25c)}
  .testi-box{top:1980px;left:580px;width:500px;height:340px;background:rgba(232,163,23,.92);color:#fff;text-align:center;padding:78px 44px 0}
  .quote{top:1940px;left:792px;width:76px;height:76px;border-radius:50%;background:#fff;display:flex;align-items:center;justify-content:center}
  .testi-box p{font-size:13px;line-height:1.85;margin-bottom:20px}
  .testi-box .name{font-family:"Alegreya",serif;font-style:italic;font-size:24px}
  .testi-box .stars{font-size:16px;letter-spacing:4px}

  /* articles */
  .article-photo{top:2548px;width:336px;height:240px}
  .article-card{top:2728px;width:288px;height:252px;background:var(--paper);box-shadow:0 4px 16px rgba(0,0,0,.12);padding:22px 24px}
  .article-card h3{font-family:"Alegreya",serif;font-style:italic;font-weight:500;font-size:24px;color:var(--ink)}
  .article-card .date{font-size:11px;color:var(--gold);font-weight:700;margin:4px 0 12px}
  .article-card p{font-size:13px;line-height:1.7;margin-bottom:20px}
  .article-card .btn{font-size:13px;padding:8px 20px;border-radius:4px}

  /* footer */
  .footer{top:3100px;left:0;width:1200px;height:428px;background:var(--night)}
  .foot-logo{top:3146px;left:0;width:1200px;display:flex;justify-content:center;align-items:center;gap:14px}
  .foot-logo .logo-name{color:#fff}
  .foot-col{top:3250px}
  .foot-col h4{font-family:"Alegreya",serif;font-weight:500;font-size:26px;color:#fff;letter-spacing:.5px;margin-bottom:8px}
  .foot-col .rule{width:46px;height:2px;background:var(--gold);margin-bottom:20px}
  .foot-col p{font-size:13px;line-height:1.8;color:var(--night-text)}
  .links{display:grid;grid-template-columns:150px 150px;row-gap:12px}
  .links a{font-size:13px;color:var(--night-text);text-decoration:none}
  .news-field{margin-top:20px;width:320px;height:42px;background:#fff;display:flex;justify-content:space-between;align-items:center;font-size:12px;color:var(--muted);padding-left:14px}
  .news-go{width:42px;height:42px;background:var(--gold);display:flex;align-items:center;justify-content:center}
  .copy{top:3456px;left:0;width:1200px;border-top:1px solid var(--night-line);padding-top:20px;text-align:center;font-size:12px;color:var(--muted)}
</style>
</head>
<body>

<!-- header -->
<div class="abs call">
  <div class="call-icon">
    <svg width="22" height="22" viewBox="0 0 24 24"><path d="M6.6 10.8a15.1 15.1 0 0 0 6.6 6.6l2.2-2.2a1 1 0 0 1 1-.25 11.4 11.4 0 0 0 3.6.57 1 1 0 0 1 1 1V20a1 1 0 0 1-1 1A17 17 0 0 1 3 4a1 1 0 0 1 1-1h3.5a1 1 0 0 1 1 1c0 1.25.2 2.45.57 3.57a1 1 0 0 1-.25 1z" fill="#e8a317"/></svg>
  </div>
  <div>
    <div class="call-label">CALL US</div>
    <div class="call-number">(000) 123 1234</div>
  </div>
</div>
<div class="abs logo"><span class="logo-mark"></span><span class="brand logo-name">calmora</span></div>
<div class="abs login">MEMBER LOGIN</div>

<nav class="abs nav">
  <a href="#">HOME</a><a href="#">ABOUT US</a><a href="#">SERVICES</a><a href="#">ARTICLES</a><a href="#">BLOG</a><a href="#">TESTIMONIALS</a><a href="#">CONTACT US</a>
</nav>

<!-- hero -->
<div class="abs hero-photo" role="img" aria-label="Happy family of parents and young children relaxing together on a living room floor"></div>
<svg class="abs" style="top:182px;left:0" width="1200" height="600" viewBox="0 0 1200 600">
  <polyline points="0,519 576,590 1200,507" fill="none" stroke="#e8a317" stroke-width="5"/>
</svg>
<div class="abs hero-copy">
  <div class="brand hero-title">calmora</div>
  <p>We keep your condo's monthly revenue steady, paying the building manager on a fixed date even when residents fall behind.</p>
  <span class="btn">Read More</span>
</div>

<!-- welcome -->
<div class="abs welcome-photo" role="img" aria-label="Smiling family with parents and children outdoors in warm sunlight"></div>
<div class="abs welcome-copy">
  <h2>Welcome to Calmora</h2>
  <div class="rule"></div>
  <p>Calmora protects condominium budgets. We take on overdue fees and guarantee the full monthly income reaches your manager on schedule, so every neighbor lives in a calmer, better kept home.</p>
  <span class="btn">Read More</span>
</div>

<!-- services -->
<div class="abs sec-title" style="top:1276px">Our Services</div>
<div class="abs sec-rule" style="top:1344px"></div>
<div class="abs sec-sub" style="top:1364px">Simple services that keep condominium finances predictable for managers and fair for every resident.</div>

<div class="abs card" style="left:88px">
  <div class="card-icon">
    <svg width="36" height="36" viewBox="0 0 36 36"><path d="M5 18 L18 6 L31 18 M9 15 V30 H27 V15" fill="none" stroke="#777" stroke-width="3" stroke-linejoin="round"/></svg>
  </div>
  <h3>Guaranteed Revenue</h3><div class="rule"></div>
  <p>The full monthly fee income reaches your building manager on the agreed date, every month.</p>
</div>
<div class="abs card active" style="left:440px">
  <div class="card-icon">
    <svg width="36" height="36" viewBox="0 0 36 36"><path d="M7 19 L15 27 L30 10" fill="none" stroke="#fff" stroke-width="3.5" stroke-linecap="round" stroke-linejoin="round"/></svg>
  </div>
  <h3>Overdue Fee Recovery</h3><div class="rule"></div>
  <p>We handle late payments with care, so neighbors stay on good terms and budgets stay whole.</p>
</div>
<div class="abs card" style="left:792px">
  <div class="card-icon">
    <svg width="36" height="36" viewBox="0 0 36 36"><path d="M6 30 H30 M10 26 V18 M18 26 V11 M26 26 V15" fill="none" stroke="#777" stroke-width="3.5" stroke-linecap="round"/></svg>
  </div>
  <h3>Clear Monthly Reports</h3><div class="rule"></div>
  <p>Simple statements show managers and residents exactly where every payment stands.</p>
</div>

<!-- testimonial -->
<div class="abs testi-photo" role="img" aria-label="Mother and children lying on green grass in a sunny park"></div>
<div class="abs testi-box">
  <p>Since Calmora took over our collections, the building receives its full budget on time every month. Repairs are planned early and residents trust the process. Our meetings are calmer and the whole community feels safer and better cared for.</p>
  <div class="name">Lena Ortiz</div>
  <div class="stars">★★★★★</div>
</div>
<div class="abs quote"><svg width="30" height="26" viewBox="0 0 30 26"><path d="M2 26V14C2 6 6 2 12 0l1 3C9 5 8 8 8 12h5v14zM17 26V14c0-8 4-12 10-14l1 3c-4 2-5 5-5 9h5v14z" fill="#e8a317"/></svg></div>

<!-- articles -->
<div class="abs sec-title" style="top:2416px">Latest Articles</div>
<div class="abs sec-rule" style="top:2484px"></div>
<div class="abs sec-sub" style="top:2502px">News and practical advice on condominium finances, shared living and peaceful neighborhoods.</div>

<div class="abs article-photo" style="left:88px;background:linear-gradient(150deg,#b79b78,#7d6a57)" role="img" aria-label="Multi-generation family smiling together"></div>
<div class="abs article-photo" style="left:432px;background:linear-gradient(150deg,#c7a585,#8c7562)" role="img" aria-label="Parents with children posing close together"></div>
<div class="abs article-photo" style="left:776px;background:linear-gradient(150deg,#e2b36e,#8a8f45)" role="img" aria-label="Family walking in a sunlit field"></div>

<div class="abs article-card" style="left:112px">
  <h3>Sed ut perspiciatis</h3><div class="date">MARCH 2024</div>
  <p>Practical notes on fees, budgets and calm neighborly living for condo boards and residents.</p>
  <span class="btn">Read More</span>
</div>
<div class="abs article-card" style="left:456px">
  <h3>Sed ut perspiciatis</h3><div class="date">MARCH 2024</div>
  <p>Practical notes on fees, budgets and calm neighborly living for condo boards and residents.</p>
  <span class="btn">Read More</span>
</div>
<div class="abs article-card" style="left:800px">
  <h3>Sed ut perspiciatis</h3><div class="date">MARCH 2024</div>
  <p>Practical notes on fees, budgets and calm neighborly living for condo boards and residents.</p>
  <span class="btn">Read More</span>
</div>

<!-- footer -->
<footer class="abs footer"></footer>
<div class="abs foot-logo"><span class="logo-mark"></span><span class="brand logo-name">calmora</span></div>

<div class="abs foot-col" style="left:88px;width:300px">
  <h4>ABOUT US</h4><div class="rule"></div>
  <p>Calmora guarantees condominium revenue on a fixed date, handling overdue fees so managers and residents can focus on home.</p>
</div>
<div class="abs foot-col" style="left:460px">
  <h4>QUICK LINES</h4><div class="rule"></div>
  <div class="links"><a href="#">Home</a><a href="#">Blog</a><a href="#">About Us</a><a href="#">Testimonials</a><a href="#">Services</a><a href="#">Contact Us</a><a href="#">Articles</a></div>
</div>
<div class="abs foot-col" style="left:780px;width:330px">
  <h4>NEWSLETTER</h4><div class="rule"></div>
  <p>Subscribe for short updates on condo finances and new articles.</p>
  <div class="news-field">Enter Your Email
    <span class="news-go"><svg width="14" height="14" viewBox="0 0 14 14"><path d="M3 1l7 6-7 6" fill="none" stroke="#fff" stroke-width="2.5"/></svg></span>
  </div>
</div>
<div class="abs copy">© Copyright 2024 Calmora. All rights reserved.</div>

</body>
</html>
```